4th Generation Family Business Needs a New Card Design!

We are a family owned 4th Generation company. We are based in the Sydney, Australia area and we are desperately in need of a more modern and classy card. We are monumental masons who design, supply & erect lasting memorials throughout cemeteries in Sydney. Our customers are normally in a period of grieving. I have attached logo files that will need to be implemented on the card. Company was established 1935. Australian Owned and Operated. Card needs to be designed to PIXO.com specification.

Target Market(s)

Our target market is based upon people that a grieving for family members that have passed away. We also deal with alot of companies that own and operate cemeteries.

Industry/Entity Type

Business

Contact Information for Business Card

Simon Harcourt, Operations Manager, 0417293086, simon@harcourtmemorials.com.au
Lewis Harcourt, Director, 0491630572, lewis@harcourtmemorials.com.au
Phone # 02 9561 3048
Website: www.harcourtmemorials.com.au
Address: Suite 17, 8 Palfrey Lane, West Carlow, Sydney NSW 2156

Font styles to use
Serif
Decorative
Script

Requirements
Must have
• Would like to see the logo nicely implemented with a modern design. Embossed lettering would be a nice additive.

```html
<!DOCTYPE html>
<html lang="en">
<head>
<meta charset="utf-8">
<title>Harcourt Memorials – Business Card</title>
<link rel="stylesheet" href="https://fonts.googleapis.com/css2?family=Open+Sans:wght@400;600;700&display=swap">
<style>
  :root {
    --canvas-bg: #3b3531;
    --card-black: #2a2829;
    --gold: #f0c22a;
    --white: #ffffff;
  }
  * { box-sizing: border-box; margin: 0; padding: 0; }
  html, body {
    width: 1200px; height: 844px; overflow: hidden;
    background: var(--canvas-bg);
    font-family: "Open Sans", Arial, sans-serif;
  }
  .canvas {
    position: relative; width: 1200px; height: 844px;
    display: flex; align-items: center; justify-content: center; gap: 60px;
  }
  .card {
    position: relative; width: 510px; height: 310px;
    background: var(--card-black);
    box-shadow: 0 10px 30px rgba(0,0,0,.35);
    overflow: hidden;
  }
  /* Contact side */
  .band { position: absolute; left: 0; right: 0; height: 11px; background: var(--gold); }
  .band--top { top: 8px; }
  .band--bottom { bottom: 8px; height: 13px; }
  .contacts {
    position: absolute; inset: 34px 20px 36px 20px;
    display: flex; flex-direction: column; justify-content: center; align-items: center;
    color: var(--white);
  }
  .person { text-align: center; }
  .person__line { font-size: 14px; line-height: 1.4; white-space: nowrap; }
  .person__name { color: var(--gold); font-weight: 700; font-size: 16px; }
  .person__role { color: var(--white); font-size: 13px; }
  .sep { margin: 0 6px; color: var(--white); }
  .label { color: var(--gold); font-weight: 700; }
  .detail { margin-right: 14px; }
  .divider {
    width: 260px; height: 1px; margin: 10px 0;
    background: linear-gradient(90deg, transparent, var(--gold), transparent);
  }
  .company-line { font-size: 13.5px; line-height: 1.6; white-space: nowrap; display: flex; align-items: center; gap: 6px; }
  .company-line + .company-line { margin-top: 4px; }
  .icon { width: 12px; height: 12px; flex: none; }
  .gap { width: 14px; }

  /* Logo side */
  .tab { position: absolute; width: 26px; height: 40px; background: var(--gold); }
  .tab::after { content: ""; position: absolute; top: 0; bottom: 0; width: 4px; background: var(--white); }
  .tab--left { left: 0; top: 215px; }
  .tab--left::after { right: -6px; }
  .tab--right { right: 0; top: 50px; }
  .tab--right::after { left: -6px; }
  .brand {
    position: absolute; left: 170px; top: 78px; width: 280px;
    display: flex; flex-direction: column; align-items: center; gap: 14px;
    text-align: center;
  }
  .brand__mark { width: 64px; height: 64px; border: 3px solid var(--white); }
  .brand__name {
    font-family: "Open Sans", Arial, sans-serif; font-weight: 600;
    font-size: 30px; line-height: 1.15; letter-spacing: 1px;
    color: var(--white);
  }
</style>
</head>
<body>
<main class="canvas">
  <section class="card card--contact" aria-label="Contact side">
    <div class="band band--top"></div>
    <div class="contacts">
      <div class="person">
        <p class="person__line"><span class="person__name">Simon Harcourt</span><span class="sep">|</span><span class="person__role">Operations Manager</span></p>
        <p class="person__line"><span class="detail"><span class="label">P:</span> 0417293086</span><span class="label">E:</span> simon@harcourtmemorials.com.au</p>
      </div>
      <div class="divider"></div>
      <div class="person">
        <p class="person__line"><span class="person__name">Lewis Harcourt</span><span class="sep">|</span><span class="person__role">Director</span></p>
        <p class="person__line"><span class="detail"><span class="label">P:</span> 0491630572</span><span class="label">E:</span> lewis@harcourtmemorials.com.au</p>
      </div>
      <div class="divider"></div>
      <p class="company-line">
        <svg class="icon" viewBox="0 0 24 24"><path fill="#f0c22a" d="M6.6 10.8a15 15 0 0 0 6.6 6.6l2.2-2.2a1 1 0 0 1 1-.25 11.4 11.4 0 0 0 3.6.57 1 1 0 0 1 1 1V20a1 1 0 0 1-1 1A17 17 0 0 1 3 4a1 1 0 0 1 1-1h3.5a1 1 0 0 1 1 1c0 1.25.2 2.45.57 3.6a1 1 0 0 1-.25 1z"/></svg>
        02 9561 3048<span class="gap"></span>
        <svg class="icon" viewBox="0 0 24 24"><circle cx="12" cy="12" r="11" fill="#f0c22a"/><path fill="#2a2829" d="M7 12.5l3.2 3.2L17 9l-1.4-1.4-5.4 5.3-1.8-1.8z"/></svg>
        www.harcourtmemorials.com.au
      </p>
      <p class="company-line">
        <svg class="icon" viewBox="0 0 24 24"><path fill="#f0c22a" d="M12 2a7 7 0 0 0-7 7c0 5.2 7 13 7 13s7-7.8 7-13a7 7 0 0 0-7-7zm0 9.5A2.5 2.5 0 1 1 12 6.5a2.5 2.5 0 0 1 0 5z"/></svg>
        Suite 17, 8 Palfrey Lane, West Carlow, Sydney NSW 2156
      </p>
    </div>
    <div class="band band--bottom"></div>
  </section>

  <section class="card card--brand" aria-label="Logo side">
    <div class="tab tab--right"></div>
    <div class="tab tab--left"></div>
    <div class="brand">
      <div class="brand__mark"></div>
      <p class="brand__name">Harcourt<br>Memorials</p>
    </div>
  </section>
</main>
</body>
</html>
```